Medical Implant company needs a Top Quality Premium Brochure

We need to create a top quality brochure for VIP clients, formed by top spine surgeons. The main goal here is to cause a deep quality impact, positioning the company and it´s solutions above the others, with a refined, unique and creative material.

Special paper, hot stamping, innovative format are welcome.

For more information check out our website: www.corvalento.com.br (web translator are recommended for content understanding)

Corvalento works with top quality spine and pain management products, providing solutions for the medical specialists, investing in high quality processes and continued medical education.

Short briefing:
1 - Company profile
2 - Quality / vision
3 - Continued education programs
4 - Main products
5 - Main partners
6 - Final stuff (creative final thoughts / considerations)

FORMAT: 25 x 18,5 cm (horizontal)
PAGES - 16

REFERENCES:

https://www.folioquarry.net/gallery/52930184/Medical-Healthcare-Profile-Brochure

https://www.folioquarry.net/gallery/7719046/TK-Alpine-Style-Brochure

Target Market(s)

Mainly brazilian spine and neuro surgeons with minimally invasive surgery skills.

Industry/Entity Type

Education

Requirements
Must have

• 18 pages design

1. Cover
2. IMAGE + TITLE - About Us
3. IMAGE + TEXT - About Us
4. IMAGE + TITLE - Vision
5. IMAGE + TEXT - Vision
6. IMAGE + TITLE - Quality
7. IMAGE + TEXT - Quality
8. Timeline Left
9. Timeline Right
10. IMAGE + TITLE - Medical Education
11. IMAGE + TEXT - Medical Education
12. IMAGE + TITLE - Minimally Invasive Technology
13. IMAGE + TEXT - Minimally Invasive Technology
14. IMAGE + TITLE - Impact Phrase
15. IMAGE + TEXT - Impact Phrase
16. Back

As longs as the text is under development and will be placed internally in the winning design, please use 'lorem ipsum' for text areas. The titles can follow the index above.

Nice to have
• The use of office pictures with some style / artistic finish in pages "about us"

```html
<!DOCTYPE html>
<html lang="en">
<head>
<meta charset="utf-8">
<title>Corvalento Brochure – Chapter One Spread</title>
<link href="https://fonts.googleapis.com/css2?family=Open+Sans:ital,wght@0,400;0,600;1,400&family=Rubik:ital,wght@0,800;1,800&display=swap" rel="stylesheet">
<style>
  :root {
    --backdrop: #e4e4e4;
    --paper: #ffffff;
    --green: #12a05a;
    --green-deep: #0c8a4b;
    --ink: #2b2b2b;
    --ink-soft: #555555;
  }
  * { box-sizing: border-box; margin: 0; padding: 0; }
  html, body { width: 1200px; height: 900px; overflow: hidden; }
  body {
    background: var(--backdrop);
    font-family: "Open Sans", Arial, sans-serif;
    color: var(--ink);
    position: relative;
  }
  .spread {
    position: absolute;
    left: 80px; top: 257px;
    width: 1040px; height: 385px;
    display: flex;
    box-shadow: 0 8px 24px rgba(0,0,0,0.18);
  }
  .page { position: relative; width: 520px; height: 385px; overflow: hidden; background: var(--paper); }

  /* Left page */
  .page-photo {
    position: absolute; inset: 0;
    background: linear-gradient(120deg, #c9b79c 0%, #e6ddd0 35%, #f4f2ee 55%, #d9dde0 80%, #b9c4c6 100%);
  }
  .chapter-tab {
    position: absolute;
    background: var(--green);
    color: #fff;
    font-size: 8px; font-weight: 600;
    letter-spacing: 0.12em;
    text-transform: uppercase;
    display: flex; align-items: center;
    padding: 0 14px;
  }
  .page-left .chapter-tab { top: 0; left: 330px; width: 190px; height: 30px; }
  .intro-box {
    position: absolute; left: 0; top: 150px;
    width: 175px; height: 120px;
    background: var(--green);
    color: #fff;
    font-size: 9px; line-height: 1.5;
    padding: 18px 16px;
  }

  /* Right page */
  .page-right { box-shadow: inset 14px 0 18px -12px rgba(0,0,0,0.25); }
  .title {
    position: absolute; left: 60px; top: 32px;
    font-family: "Rubik", Arial, sans-serif;
    font-weight: 800; font-style: italic;
    font-size: 25px; color: var(--green-deep);
    letter-spacing: -0.01em;
  }
  .lead {
    position: absolute; left: 22px; top: 76px; width: 120px;
    font-size: 8px; font-style: italic; line-height: 1.55; color: var(--ink-soft);
  }
  .feature-photo {
    position: absolute; left: 150px; top: 100px; width: 290px; height: 185px;
    background: linear-gradient(135deg, #b9c2b5 0%, #eef0ee 40%, #d5dccd 70%, #9fae97 100%);
  }
  .page-right .chapter-tab { top: 126px; left: 418px; width: 102px; height: 28px; justify-content: center; padding: 0; }
  .column {
    position: absolute; font-size: 7.5px; line-height: 1.6; color: var(--ink-soft);
  }
  .column-a { left: 22px; top: 160px; width: 120px; }
  .column-b { left: 220px; top: 296px; width: 220px; }
  .folio {
    position: absolute; left: 480px; top: 352px; width: 22px; height: 22px;
    background: var(--green); color: #fff;
    font-size: 9px; font-weight: 600;
    display: flex; align-items: center; justify-content: center;
  }
</style>
</head>
<body>
  <main class="spread">
    <section class="page page-left">
      <div class="page-photo" role="img" aria-label="Photograph of a smiling surgeon in scrubs holding a clipboard, with a medical team attending a patient behind him"></div>
      <div class="chapter-tab">Chapter One</div>
      <div class="intro-box">Lorem ipsum dolor sit amet, consectetur adipiscing elit, sed do eiusmod tempor incididunt ut labore et dolore magna aliqua. Ut enim ad minim veniam, quis</div>
    </section>
    <section class="page page-right">
      <h1 class="title">Lorem ipsum dolor sit amet</h1>
      <p class="lead">The secret of getting ahead is getting started. The secret of getting started is breaking your complex overwhelming tasks into small manageable tasks, and then starting on the first one.</p>
      <div class="feature-photo" role="img" aria-label="Photograph of white, red and blue pills scattered on banknotes"></div>
      <div class="chapter-tab">Chapter One</div>
      <p class="column column-a">Donec sed odio dui. Duis mollis, est non commodo luctus, nisi erat porttitor ligula, eget lacinia odio sem nec elit. Sed posuere consectetur est at lobortis. Nulla vitae elit libero. Fusce dapibus, tellus ac cursus commodo, tortor mauris condimentum nibh, ut fermentum massa justo sit amet risus. Lorem ipsum dolor sit amet, consectetur adipiscing elit, euismod aenean eu leo quam.</p>
      <p class="column column-b">Pellentesque ornare sem lacinia quam venenatis vestibulum. Aenean lacinia bibendum nulla sed consectetur. Cras mattis consectetur purus sit amet fermentum. Nulla vitae elit libero, a pharetra augue. Vestibulum id ligula porta felis euismod semper. Sed dapibus massa aliquam elit ulla ac tristique risus.</p>
      <div class="folio">7</div>
    </section>
  </main>
</body>
</html>
```